Radiant Comets Season Finale Camp

We need a brochure design for a netball camp we are running for children aged between 11 and 16 in Anglesea from Friday the 2nd of October until Sunday the 4th of October.
Participants will undertake training session with elite netballers but also do beach activities, lectures on sport nutrition and goal setting.
The design needs to be a summery, fun kind of look that will appeal to children that age and their parents. It needs to have information such as the cost etc which will be provided somewhere later on

It will be a netball experience they will never forget.

Target Market(s)

11-16 old girls and their parents

Font styles to use
Sans Serif

Requirements
Must have
• Larkfield logo
• Radiant comets logo
Nice to have
• Cost is $350
• Dates 2nd - 4th of October
• Follow us on Instagram radiant_comets
• Booking details as follows

```html
<!DOCTYPE html>
<html lang="en">
<head>
<meta charset="utf-8">
<title>Radiant Comets Season Finale Camp – Brochure</title>
<link rel="stylesheet" href="https://fonts.googleapis.com/css2?family=Bebas+Neue&family=Oswald:wght@500;600&family=Quicksand:wght@500;700&display=swap">
<style>
  :root {
    --bg: #ecebe8;
    --paper: #ffffff;
    --magenta: #d0268f;
    --magenta-light: #e65fb0;
    --purple: #8a2c8c;
    --purple-deep: #5b2a86;
    --indigo: #3b2b8a;
    --lavender: #dcc6e6;
    --ink: #4a4a4a;
    --heading: #2b2b2b;
  }
  * { box-sizing: border-box; margin: 0; padding: 0; }
  html, body { width: 1200px; height: 729px; overflow: hidden; background: var(--bg); }
  body { position: relative; font-family: "Quicksand", sans-serif; color: var(--ink); }

  .brochure {
    position: absolute; left: 40px; top: 110px; width: 740px; height: 510px;
    background: var(--paper); box-shadow: 0 4px 14px rgba(0,0,0,.18); overflow: hidden;
  }
  .brochure__shapes, .card__shapes { position: absolute; inset: 0; width: 100%; height: 100%; }
  .fold { position: absolute; top: 0; bottom: 0; width: 1px; background: rgba(0,0,0,.06); }
  .fold--one { left: 247px; } .fold--two { left: 494px; }

  .section { position: absolute; width: 210px; }
  .section__title {
    font-family: "Oswald", sans-serif; font-weight: 600; font-size: 19px;
    color: var(--heading); letter-spacing: .2px; margin-bottom: 4px;
  }
  .section__title span { color: var(--magenta); }
  .section__body { font-size: 10.3px; line-height: 15px; font-weight: 500; }
  .section--about-us { left: 25px; top: 118px; }
  .section--about-camp { left: 262px; top: 220px; }

  .activities { position: absolute; left: 12px; top: 326px; width: 225px; text-align: center; }
  .activities__lead {
    font-family: "Oswald", sans-serif; font-weight: 500; font-size: 11px;
    line-height: 13px; color: var(--heading); text-transform: uppercase;
  }
  .activities__list { list-style: none; display: flex; justify-content: space-around; margin-top: 10px; }
  .activity { width: 70px; display: flex; flex-direction: column; align-items: center; }
  .activity__icon { width: 40px; height: 40px; }
  .activity__label { margin-top: 5px; font-size: 9.5px; line-height: 11px; font-weight: 700; color: var(--purple); }

  .partner { position: absolute; left: 488px; display: flex; align-items: center; gap: 6px; }
  .partner--larkfield { top: 352px; }
  .partner--comets { top: 410px; }
  .partner__dot { width: 14px; height: 14px; border-radius: 50%; }
  .partner--larkfield .partner__dot { background: var(--indigo); }
  .partner--comets .partner__dot { background: var(--magenta); }
  .partner__name { font-family: "Oswald", sans-serif; font-weight: 600; font-size: 14px; line-height: 15px; }
  .partner--larkfield .partner__name { color: var(--indigo); }
  .partner--comets .partner__name { color: var(--purple-deep); }

  .age-tag {
    position: absolute; left: 648px; top: 392px; width: 66px; height: 50px;
    background: var(--magenta); color: #fff; text-align: center;
    font-family: "Oswald", sans-serif; font-weight: 600;
  }
  .age-tag__label { font-size: 12px; line-height: 14px; padding-top: 4px; }
  .age-tag__range { font-size: 22px; line-height: 24px; }
  .age-tag::after {
    content: ""; position: absolute; left: 10px; bottom: -12px;
    border-left: 8px solid var(--magenta); border-bottom: 12px solid transparent;
  }

  .card {
    position: absolute; left: 850px; top: 75px; width: 290px; height: 580px;
    background: var(--paper); box-shadow: 0 4px 14px rgba(0,0,0,.18); overflow: hidden;
  }
  .card__brand { position: absolute; left: 16px; top: 128px; display: flex; align-items: center; gap: 6px; }
  .card__brand-dot { width: 14px; height: 14px; border-radius: 50%; background: var(--magenta); }
  .card__brand-name { font-family: "Oswald", sans-serif; font-weight: 600; font-size: 20px; color: var(--indigo); }
  .card__dates {
    position: absolute; left: 18px; top: 350px; width: 260px;
    font-family: "Bebas Neue", sans-serif; font-size: 31px; line-height: 30px; color: var(--magenta-light);
  }
  .card__title {
    position: absolute; left: 18px; top: 452px;
    font-family: "Bebas Neue", sans-serif; font-size: 58px; line-height: 52px;
  }
  .card__title-top { display: block; color: var(--magenta); }
  .card__title-bottom { display: block; color: var(--indigo); }
</style>
</head>
<body>

<article class="brochure">
  <svg class="brochure__shapes" viewBox="0 0 740 510" aria-hidden="false">
    <defs>
      <linearGradient id="gymTones" x1="0" y1="0" x2="1" y2="1">
        <stop offset="0" stop-color="#6e6f72"/><stop offset=".6" stop-color="#9a4a4f"/><stop offset="1" stop-color="#3f4247"/>
      </linearGradient>
      <linearGradient id="courtTones" x1="0" y1="0" x2="1" y2="1">
        <stop offset="0" stop-color="#4a4c52"/><stop offset=".5" stop-color="#b9c3cc"/><stop offset="1" stop-color="#5b5f66"/>
      </linearGradient>
    </defs>
    <polygon points="320,0 740,0 740,28 330,12" fill="var(--magenta)"/>
    <polygon points="195,0 330,0 305,55 180,100" fill="var(--purple)"/>
    <polygon points="0,0 200,0 182,95 0,95" fill="url(#gymTones)" role="img" aria-label="Photo: girls training at netball indoors"/>
    <polygon points="440,40 740,18 740,62 560,52" fill="var(--magenta-light)" opacity=".8"/>
    <polygon points="315,50 705,55 725,62 725,280 300,186" fill="url(#courtTones)" role="img" aria-label="Photo: netball players contesting a shot on an outdoor court"/>
    <polygon points="300,186 725,280 725,298 298,194" fill="var(--purple)"/>
    <polygon points="560,200 740,150 740,305 625,302" fill="var(--magenta)"/>
    <polygon points="600,240 740,210 740,260" fill="var(--magenta-light)" opacity=".7"/>
    <polygon points="10,440 330,420 405,470 405,510 10,510" fill="var(--magenta)"/>
    <polygon points="200,480 400,452 495,510 200,510" fill="var(--purple)"/>
    <polygon points="420,488 740,455 740,510 420,510" fill="var(--lavender)"/>
  </svg>
  <span class="fold fold--one"></span>
  <span class="fold fold--two"></span>

  <section class="section section--about-us">
    <h2 class="section__title">ABOUT <span>US</span></h2>
    <p class="section__body">Lorem ipsum dolor sit amet, consectetur adipiscing elit, sed do eiusmod tempor incididunt ut labore et dolore magna aliqua. Ut enim ad minim veniam, quis nostrud exercitation ullamco laboris nisi ut aliquip ex ea commodo consequat. Duis aute irure dolor in reprehenderit in voluptate velit esse cillum dolore eu fugiat nulla pariatur. Excepteur sint occaecat cupidatat non proident, sunt in culpa qui officia deserunt mollit anim id est laborum.</p>
  </section>

  <section class="activities">
    <p class="activities__lead">Participants will undertake training<br>session with elite netballers but also do:</p>
    <ul class="activities__list">
      <li class="activity">
        <svg class="activity__icon" viewBox="0 0 40 40"><circle cx="20" cy="20" r="20" fill="var(--purple)"/><path d="M9 25q3-3 6 0t6 0t6 0t5 0" stroke="#fff" stroke-width="2" fill="none"/><path d="M20 10v13M20 11l7 10h-7" stroke="#fff" stroke-width="2" fill="none"/></svg>
        <span class="activity__label">Beach activities</span>
      </li>
      <li class="activity">
        <svg class="activity__icon" viewBox="0 0 40 40"><circle cx="20" cy="20" r="20" fill="var(--purple)"/><circle cx="20" cy="12" r="3.5" fill="#fff"/><rect x="13" y="18" width="14" height="14" rx="1" fill="#fff"/></svg>
        <span class="activity__label">Lectures on sport nutrition</span>
      </li>
      <li class="activity">
        <svg class="activity__icon" viewBox="0 0 40 40"><circle cx="20" cy="20" r="20" fill="var(--purple)"/><path d="M10 10l5 5M15 10l-5 5M25 26l5 5M30 26l-5 5" stroke="#fff" stroke-width="2"/><circle cx="28" cy="13" r="3" stroke="#fff" stroke-width="2" fill="none"/><path d="M14 20q6 8 12 3" stroke="#fff" stroke-width="2" fill="none"/></svg>
        <span class="activity__label">Goal setting</span>
      </li>
    </ul>
  </section>

  <section class="section section--about-camp">
    <h2 class="section__title">ABOUT <span>THE CAMP</span></h2>
    <p class="section__body">Lorem ipsum dolor sit amet, consectetur adipiscing elit, sed do eiusmod tempor incididunt ut labore et dolore magna aliqua. Ut enim ad minim veniam, quis nostrud exercitation ullamco laboris nisi ut aliquip ex ea commodo consequat. Duis aute irure dolor in reprehenderit in voluptate velit esse cillum dolore eu fugiat nulla pariatur. Excepteur sint occaecat cupidatat non proident, sunt in culpa qui officia deserunt mollit anim id est laborum.</p>
  </section>

  <div class="partner partner--larkfield">
    <span class="partner__dot"></span>
    <span class="partner__name">Larkfield Camping<br>Victoria</span>
  </div>
  <div class="partner partner--comets">
    <span class="partner__dot"></span>
    <span class="partner__name">Radiant Comets</span>
  </div>
  <div class="age-tag">
    <p class="age-tag__label">For Ages</p>
    <p class="age-tag__range">11-16</p>
  </div>
</article>

<article class="card">
  <svg class="card__shapes" viewBox="0 0 290 580">
    <defs>
      <linearGradient id="cardTop" x1="0" y1="0" x2="1" y2="1">
        <stop offset="0" stop-color="var(--magenta)"/><stop offset="1" stop-color="var(--purple)"/>
      </linearGradient>
      <linearGradient id="skyTones" x1="0" y1="0" x2="1" y2="1">
        <stop offset="0" stop-color="#3f6fb5"/><stop offset=".6" stop-color="#a9c3de"/><stop offset="1" stop-color="#c9a27d"/>
      </linearGradient>
    </defs>
    <rect width="290" height="440" fill="url(#cardTop)"/>
    <polygon points="75,15 83,38 108,38 88,52 95,76 75,62 55,76 62,52 42,38 67,38" fill="var(--magenta-light)" opacity=".7"/>
    <polygon points="230,40 240,70 272,70 246,88 256,118 230,100 204,118 214,88 188,70 220,70" fill="var(--magenta-light)" opacity=".6"/>
    <polygon points="0,215 290,170 290,322 130,345 0,330" fill="url(#skyTones)" role="img" aria-label="Photo: young netball player holding a ball under a netball post"/>
    <polygon points="90,230 110,290 170,290 120,325 140,385 90,350 40,385 60,325 10,290 70,290" fill="var(--magenta)"/>
    <polygon points="0,325 290,300 290,420 0,445" fill="var(--purple)"/>
    <polygon points="0,445 290,420 290,580 0,580" fill="var(--paper)"/>
  </svg>
  <div class="card__brand">
    <span class="card__brand-dot"></span>
    <span class="card__brand-name">Radiant Comets</span>
  </div>
  <p class="card__dates">2nd of October<br>until 4th of October</p>
  <h1 class="card__title">
    <span class="card__title-top">Season</span>
    <span class="card__title-bottom">Finale Camp</span>
  </h1>
</article>

</body>
</html>
```